Seed Oil Safety Card for Healthy Restaurant Dining

I am seeking a design for a physical card to communicate my wife's health-related dietary restriction regarding seed oils. This card will be given to restaurant waiters to ensure her meals are prepared without seed oils, as it is a health issue and not merely a preference.
My wife cannot eat any “seed oil” or “processed oil”, including:
- Vegetable oil
- Canola oil
- Soybean oil
- Sunflower oil
- Corn oil
- Cottonseed oil
- Safflower oil
- Peanut oil
- Sesame oil
Oils that are OK for her to consume:
- Butter (most preferable)
- Extra virgin olive oil
- Avocado oil
- Coconut oil
- Ghee
- Lard
- Any other animal-based fats
Key Design Requirements:
- Clarity and speed of communication: The card should be easily read and understood by waiters, even in low-light environments, emphasizing that it's a health concern.
- Avoid common misconceptions: Ensure the design doesn't imply common dietary preferences like "vegetarian" or "no butter." Animal fats and butter are actually preferable for her!
- Preferred term: Use "seed oils" as the term to describe what she cannot eat due to her health issue.
- Trace amounts are acceptable: Communicate that it's OK to use cookware that has previously been in contact with seed oils, but not to have seed oil as an ingredient. Please suggest a concise way to convey this.
- Card dimensions: Design should be 3.5” x 2.25” (standard credit-card size on printorvale.example). Horizontal or vertical layouts are both fine, whichever makes the message clearer.
Design Suggestions:
- Utilize bold and easy-to-read typography to communicate the main message.
- Consider incorporating relevant icons or graphics that help convey the message without adding confusion.
- Use contrasting colors to enhance readability, especially in low-light situations.
- To communicate the “trace amounts OK” part, consider phrases such as:
- "Cross-contamination acceptable"
- “Used cookware OK, no ingredient use”
- “Separate cookware not necessary”
Thank you for your assistance in creating this essential card for my wife's health and safety when dining out!

```html
<!DOCTYPE html>
<html lang="en">
<head>
<meta charset="utf-8">
<title>Seed Oil Allergy Card</title>
<link rel="stylesheet" href="https://fonts.googleapis.com/css2?family=Roboto+Condensed:ital,wght@0,400;0,700;1,400&display=swap">
<style>
  :root {
    --backdrop: #a3a3a3;
    --card: #ffffff;
    --navy: #0e2a38;
    --danger: #c41b24;
    --safe: #1f8f30;
  }
  * { margin: 0; padding: 0; box-sizing: border-box; }
  html, body { width: 1200px; height: 1200px; overflow: hidden; }
  body {
    background: var(--backdrop);
    font-family: "Roboto Condensed", "Arial Narrow", sans-serif;
  }
  .card {
    position: absolute;
    left: 246px; top: 50px;
    width: 707px; height: 1100px;
    background: var(--card);
    border-radius: 66px;
  }
  .card-title {
    position: absolute;
    left: 0; right: 0; top: 42px;
    text-align: center;
    font-weight: 700;
    font-size: 70px;
    letter-spacing: 2px;
    color: var(--navy);
    line-height: 80px;
  }
  .title-rule {
    position: absolute;
    left: 189px; top: 132px;
    width: 329px; height: 6px;
    background: var(--navy);
  }
  .column-head {
    position: absolute;
    top: 202px;
    width: 300px;
    text-align: center;
  }
  .column-head.banned { left: 42px; }
  .column-head.allowed { left: 361px; }
  .column-head svg { display: block; margin: 0 auto; }
  .column-head h2 {
    margin-top: 20px;
    font-size: 36px;
    line-height: 31px;
    font-weight: 700;
    letter-spacing: 1px;
    color: var(--navy);
  }
  .column-head .pointer { margin-top: 23px; }
  .oil-list {
    position: absolute;
    top: 456px;
    list-style: none;
    font-size: 31px;
    line-height: 43.6px;
    letter-spacing: 0.5px;
  }
  .oil-list.banned { left: 78px; color: var(--danger); }
  .oil-list.allowed { left: 372px; color: var(--safe); }
  .oil-list li { position: relative; padding-left: 34px; }
  .oil-list li svg { position: absolute; left: 0; top: 12px; }
  .trace-note {
    position: absolute;
    left: 0; right: 0; top: 932px;
    text-align: center;
    font-style: italic;
    font-size: 30px;
    line-height: 36px;
    letter-spacing: 0.5px;
    color: var(--navy);
  }
</style>
</head>
<body>
<main class="card">
  <h1 class="card-title">SEED OIL ALLERGY!</h1>
  <div class="title-rule"></div>

  <div class="column-head banned">
    <svg width="86" height="86" viewBox="0 0 86 86" aria-hidden="true">
      <rect x="2.5" y="2.5" width="81" height="81" rx="3" fill="none" stroke="var(--danger)" stroke-width="5"/>
      <path d="M24 24 L62 62 M62 24 L24 62" stroke="var(--danger)" stroke-width="11" stroke-linecap="square"/>
    </svg>
    <h2>Cannot<br>Consume</h2>
    <svg class="pointer" width="54" height="30" viewBox="0 0 54 30" aria-hidden="true"><path d="M0 0 H54 L27 30 Z" fill="var(--navy)"/></svg>
  </div>

  <div class="column-head allowed">
    <svg width="86" height="86" viewBox="0 0 86 86" aria-hidden="true">
      <rect x="2.5" y="2.5" width="81" height="81" rx="3" fill="none" stroke="var(--safe)" stroke-width="5"/>
      <path d="M20 46 L35 61 L66 22" fill="none" stroke="var(--safe)" stroke-width="11"/>
    </svg>
    <h2>OK<br>To Consume</h2>
    <svg class="pointer" width="54" height="30" viewBox="0 0 54 30" aria-hidden="true"><path d="M0 0 H54 L27 30 Z" fill="var(--navy)"/></svg>
  </div>

  <svg width="0" height="0" style="position:absolute">
    <defs>
      <symbol id="mark-no" viewBox="0 0 20 20">
        <rect x="1.5" y="1.5" width="17" height="17" fill="none" stroke="var(--danger)" stroke-width="2"/>
        <path d="M6 6 L14 14 M14 6 L6 14" stroke="var(--danger)" stroke-width="2.6"/>
      </symbol>
      <symbol id="mark-ok" viewBox="0 0 20 20">
        <rect x="1.5" y="1.5" width="17" height="17" fill="none" stroke="var(--safe)" stroke-width="2"/>
        <path d="M5.5 10 L8.5 13 L14.5 6" fill="none" stroke="var(--safe)" stroke-width="2.4"/>
      </symbol>
    </defs>
  </svg>

  <ul class="oil-list banned">
    <li><svg width="20" height="20"><use href="#mark-no"/></svg>Vegetable oil</li>
    <li><svg width="20" height="20"><use href="#mark-no"/></svg>Canola oil</li>
    <li><svg width="20" height="20"><use href="#mark-no"/></svg>Soybean oil</li>
    <li><svg width="20" height="20"><use href="#mark-no"/></svg>Sunflower oil</li>
    <li><svg width="20" height="20"><use href="#mark-no"/></svg>Corn oil</li>
    <li><svg width="20" height="20"><use href="#mark-no"/></svg>Cottonseed oil</li>
    <li><svg width="20" height="20"><use href="#mark-no"/></svg>Safflower oil</li>
    <li><svg width="20" height="20"><use href="#mark-no"/></svg>Peanut oil</li>
    <li><svg width="20" height="20"><use href="#mark-no"/></svg>Sesame oil</li>
  </ul>

  <ul class="oil-list allowed">
    <li><svg width="20" height="20"><use href="#mark-ok"/></svg>Butter<br>(most preferable)</li>
    <li><svg width="20" height="20"><use href="#mark-ok"/></svg>Extra virgin</li>
    <li><svg width="20" height="20"><use href="#mark-ok"/></svg>Olive oil</li>
    <li><svg width="20" height="20"><use href="#mark-ok"/></svg>Avocado oil</li>
    <li><svg width="20" height="20"><use href="#mark-ok"/></svg>Coconut oil</li>
    <li><svg width="20" height="20"><use href="#mark-ok"/></svg>Ghee</li>
    <li><svg width="20" height="20"><use href="#mark-ok"/></svg>Lard</li>
    <li><svg width="20" height="20"><use href="#mark-ok"/></svg>Any other<br>animal-based fats</li>
  </ul>

  <p class="trace-note">"Cross-contamination acceptable"<br>“Used cookware OK, no ingredient use"<br>“Separate cookware not necessary"</p>
</main>
</body>
</html>
```